Commit to H.E.A.L. (Healthy Eating and Living)Corporate Wellness

Pledge to T.R.I.M. (Tidy Motion In Routines) is my health and wellness company. I am a certified Health & Lifestyle Coach who provides a 6 month one-on-one coaching program for individuals and groups. I also provide 1 hour health seminars or "brown bag" lunches for any type of organization. My focus is on prevention of chronic disease through health and food education, as well as effective lifestyle coaching. I would like the brochure to have my logo, my name and certification, some health statistics, and my programs/seminars. Looking for a one page, half fold or trifold brochure design. I am flexible! I forgot to include my personal information. phone number 555/014-7739. email is marla@brightpathforwardnation.example. website is www.pledgetotrim.example.

Target Market(s)

Companies (large or small) looking for wellness and disease prevention programs for their employees.

Industry/Entity Type

Health

Requirements
Must have
• I am going into this with no picture in my head as to what I want. I like simplicity. I like to represent health, in all aspects, from food to environment. I will attach my logo to use, and colors should accent the logo.
I need it to include my name and title (Marla Vostrik, Certified Health & Lifestyle Coach). The tag line "Because your staff's vigor IS your bottom line." These statistics listed clearly: "1. The U.S. spends $2.8 trillion on health care every year, and this number is rising. 2. Treating individuals with chronic preventable disease is responsible for 75% of our health care costs. 3. The U.S. spends more on healthcare than Japan, Germany, France, China, UK, Italy, Canada, Brazil, Spain and Australia COMBINED. 4. The Global Vitality Council ranks the U.S. 37th for overall health outcomes. This means that more healthcare spending does not equate to better health.
Then it needs to say that "Our healthcare costs are out of control, increasing, and unsustainable. We do not have a healthcare system, we have a disease care system. Prevention of chronic disease is the only way to reduce our costs. Workplace wellness solutions MUST change behaviors. Food and health education, as well as effective lifestyle coaching are the keys to this behavior change."
I offer 1 hour seminars, sample seminars include but are not limited to "Cancer Prevention" "Nation's Plate/Nation's Ailment," and "Vigor & Balance starts where Ordinary Habits Stop." I also offer a six month bi-weekly health coaching program for individuals or small groups. Plus custom programs that include health food store tours, pantry purges, cooking ideas and preparation, etc.

```html
<!DOCTYPE html>
<html lang="en">
<head>
<meta charset="utf-8">
<title>Life Coaching Brochure Panels</title>
<link href="https://fonts.googleapis.com/css2?family=Lora:wght@400;700&display=swap" rel="stylesheet">
<style>
  :root {
    --leaf: #4f7b36;
    --frame: #55803a;
    --ink: #1a1a1a;
    --paper: #ffffff;
    --sky-top: #1f5fae;
    --sky-bottom: #cfe3f5;
    --cream: #f4f1ea;
    --amber: #8a5a2c;
  }
  * { box-sizing: border-box; margin: 0; padding: 0; }
  html, body {
    width: 1200px;
    height: 1200px;
    overflow: hidden;
    background: var(--paper);
  }
  .canvas {
    position: relative;
    width: 1200px;
    height: 1200px;
    font-family: "Lora", Georgia, serif;
    color: var(--ink);
  }
  .panel {
    position: absolute;
    top: 37px;
    height: 1125px;
    border: 8px solid var(--frame);
    background: var(--paper);
  }
  .panel--left { left: 37px; width: 528px; }
  .panel--right {
    left: 635px;
    width: 526px;
    display: flex;
    flex-direction: column;
    align-items: center;
    padding: 30px 22px 24px;
    gap: 16px;
  }

  .panel-heading {
    font-weight: 700;
    font-size: 31px;
    color: var(--leaf);
    text-align: center;
    line-height: 1.1;
  }
  .panel-copy {
    font-size: 18px;
    line-height: 23px;
    text-align: center;
  }

  .intro { position: absolute; left: 22px; right: 22px; top: 30px; }
  .intro .panel-copy { margin-top: 2px; }

  .photo-frame { border: 8px solid var(--frame); }
  .photo-frame--signs {
    position: absolute;
    left: 29px; top: 330px; width: 462px; height: 454px;
  }
  .photo-frame--bottle { width: 461px; height: 330px; flex: none; }
  .photo { width: 100%; height: 100%; }
  .photo--signs {
    background: linear-gradient(180deg, var(--sky-top) 0%, #4f8fd0 45%, var(--sky-bottom) 100%);
  }
  .photo--bottle {
    background: radial-gradient(ellipse 30% 45% at 50% 55%, var(--amber) 0%, #b98b5a 55%, var(--cream) 100%);
  }

  .programs { position: absolute; left: 22px; right: 22px; top: 810px; }
  .programs .panel-copy { margin-top: 4px; }

  .facts { width: 100%; }
  .fact-list { list-style: none; margin-top: 2px; }
  .fact-list li { margin-bottom: 5px; }
  .fact-list li::before { content: "\2022\00a0\00a0"; }

  .cost-statement { width: 100%; }

  .coach-card { width: 100%; text-align: center; }
  .coach-name {
    font-weight: 700;
    font-size: 24px;
    line-height: 1.2;
    color: var(--leaf);
  }
  .coach-title { font-size: 18px; line-height: 23px; }
  .tagline {
    font-weight: 700;
    font-size: 18px;
    line-height: 23px;
    color: var(--leaf);
    margin-top: 6px;
  }
  .contact { font-size: 17px; line-height: 22px; margin-top: 6px; }
</style>
</head>
<body>
<main class="canvas">

  <section class="panel panel--left">
    <div class="intro">
      <h2 class="panel-heading">What is Life Coaching ?</h2>
      <p class="panel-copy">Life Coaching is different from consulting, mentoring, advice, therapy, or counseling. The coaching process addresses specific personal projects, business successes and general conditions in the client’s personal life or profession by examining what is going on right now, discovering what your obstacles or challenges might be, and choosing a course of action to make your life be what you want it to be.</p>
    </div>

    <div class="photo-frame photo-frame--signs">
      <div class="photo photo--signs" role="img" aria-label="Photo of highway signs reading Healthy Eating, Fitness Training and Stress Relief against a blue sky"></div>
    </div>

    <div class="programs">
      <h2 class="panel-heading">How Life Coaching Works</h2>
      <p class="panel-copy">I offer 1 hour seminars, sample seminars include but are not limited to cancer prevention Nation’s Plate/Nation’s Ailment, and Vigor &amp; Balance starts where Ordinary Habits Stop. I also offer a six-month bi-weekly health-coaching program for individuals or small groups. Plus custom programs that include health food store tours, pantry purges, cooking ideas and preparation, etc.</p>
    </div>
  </section>

  <section class="panel panel--right">
    <div class="facts">
      <h2 class="panel-heading">Facts About Health Care</h2>
      <ul class="fact-list panel-copy">
        <li>The U.S. spends $2.8 trillion on health care every year, and this number is rising.</li>
        <li>Treating individuals with chronic preventable disease is responsible for 75% of our health care costs.</li>
        <li>The U.S. spends more on healthcare than Japan, Germany, France, China, UK, Italy, Canada, Brazil, Spain and Australia COMBINED.</li>
        <li>The Global Vitality Council ranks the U.S. 37th for overall health outcomes. This means that more healthcare spending does not equate to better health.</li>
      </ul>
    </div>

    <p class="cost-statement panel-copy">Our healthcare costs are out of control, increasing, and unsustainable. We do not have a healthcare system, we have a disease care system. Prevention of chronic disease is the only way to reduce our costs. Workplace wellness solutions MUST change behaviors. Food and health education, as well as effective lifestyle coaching are the keys to this behavior change.</p>

    <div class="photo-frame photo-frame--bottle">
      <div class="photo photo--bottle" role="img" aria-label="Photo of an amber pill bottle filled with rolled paper currency on a white background"></div>
    </div>

    <div class="coach-card">
      <p class="coach-name">Marla Vostrik</p>
      <p class="coach-title">Certified Health &amp; Lifestyle Coach</p>
      <p class="tagline">Because your staff’s vigor IS your bottom line.</p>
      <p class="contact">555/014-7739<br>marla@brightpathforwardnation.example<br>www.pledgetotrim.example</p>
    </div>
  </section>

</main>
</body>
</html>
```